Spring 2026 Billboard - superchill with Varnel heating

Rethinking - I would like to do something with this photo - somthing about you can relaxing this summer Varnel AC can fix it or 'making AC look easy' or Making your home cool look easy

Industry/Entity Type

HVAC

```html
<!DOCTYPE html>
<html lang="en">
<head>
<meta charset="UTF-8">
<title>Varnel Heating &amp; AC – Spring 2026 Billboard</title>
<link rel="stylesheet" href="https://fonts.googleapis.com/css2?family=Poppins:ital,wght@0,500;0,600;0,700;0,800;1,600&display=swap">
<style>
  :root {
    --page-bg: #dfe9f4;
    --board-deep: #0a1f5c;
    --board-mid: #123a8f;
    --board-glow: #2a62c4;
    --text-white: #ffffff;
    --text-ice: #cdeeff;
    --text-ice-deep: #9fd8f7;
    --accent-yellow: #f5cc2a;
    --brand-blue: #2f7fe0;
    --hero-tone: #1f4fb0;
    --cube-tone: #8fd0f5;
    --house-tone: #4a6f9a;
    --flake-tone: rgba(140, 205, 245, 0.55);
  }
  * { box-sizing: border-box; margin: 0; padding: 0; }
  html, body {
    width: 1200px;
    height: 800px;
    overflow: hidden;
    background: var(--page-bg);
    font-family: "Poppins", sans-serif;
  }
  .billboard {
    position: absolute;
    left: 0;
    top: 123px;
    width: 1200px;
    height: 554px;
    overflow: hidden;
    background:
      radial-gradient(ellipse 520px 300px at 560px 230px, rgba(80, 150, 235, 0.45), transparent 70%),
      linear-gradient(180deg, var(--board-mid) 0%, var(--board-deep) 100%);
  }
  .art {
    position: absolute;
  }
  .art--hero {
    left: 30px; top: 15px; width: 440px; height: 295px;
    border-radius: 40% 50% 45% 40%;
    background: radial-gradient(ellipse at 45% 50%, var(--hero-tone), rgba(31, 79, 176, 0.15) 75%, transparent);
  }
  .art--cube {
    left: 480px; top: 165px; width: 230px; height: 160px;
    border-radius: 22px;
    background: radial-gradient(ellipse at 55% 50%, var(--cube-tone), rgba(143, 208, 245, 0.2) 70%, transparent);
  }
  .art--house {
    left: 745px; top: 130px; width: 455px; height: 230px;
    background: linear-gradient(180deg, rgba(74, 111, 154, 0.2) 0%, var(--house-tone) 45%, #2f5a3a 100%);
    border-radius: 30px 0 0 30px;
  }
  .art--flake {
    width: 48px; height: 48px; border-radius: 50%;
    background: var(--flake-tone);
  }
  .flake-1 { left: 50px; top: 10px; width: 60px; height: 60px; }
  .flake-2 { left: 1085px; top: 35px; }
  .flake-3 { left: 1148px; top: 410px; width: 56px; height: 56px; }
  .flake-4 { left: 80px; top: 340px; width: 32px; height: 32px; }
  .flake-5 { left: 160px; top: 345px; width: 26px; height: 26px; }

  .headline {
    position: absolute;
    left: 380px;
    top: 38px;
    width: 690px;
    text-align: center;
    color: var(--text-white);
    font-weight: 600;
    line-height: 1.05;
  }
  .headline__line { display: block; }
  .headline__line--one { font-size: 46px; }
  .headline__line--two { font-size: 52px; margin-top: 6px; }
  .headline__ice {
    color: var(--text-ice);
    font-weight: 800;
    text-shadow: 0 0 14px rgba(159, 216, 247, 0.6);
  }
  .headline__line--one .headline__ice { font-size: 60px; }
  .headline__line--two .headline__ice { font-size: 66px; }

  .subline {
    position: absolute;
    left: 0;
    top: 388px;
    width: 1220px;
    text-align: center;
    color: var(--text-white);
    font-size: 33px;
    font-weight: 600;
    font-style: italic;
  }
  .subline__brand { color: var(--accent-yellow); }

  .brand {
    position: absolute;
    display: flex;
    align-items: center;
    gap: 10px;
    color: var(--brand-blue);
    font-weight: 700;
  }
  .brand__dot {
    border-radius: 50%;
    background: var(--accent-yellow);
  }
  .brand--full { left: 20px; top: 462px; font-size: 34px; }
  .brand--full .brand__dot { width: 40px; height: 40px; }
  .brand--full .brand__sub {
    display: block;
    font-size: 18px;
    margin-top: -6px;
  }
  .brand--full .brand__text { line-height: 1.1; }
  .brand--large { left: 318px; top: 462px; font-size: 44px; gap: 14px; }
  .brand--large .brand__dot { width: 54px; height: 54px; }

  .tagline {
    position: absolute;
    left: 730px;
    top: 478px;
    color: var(--accent-yellow);
    font-size: 24px;
    font-weight: 600;
  }
  .tagline__link { color: var(--text-white); }
</style>
</head>
<body>
  <main class="billboard">
    <div class="art art--flake flake-1" role="img" aria-label="Snowflake decoration"></div>
    <div class="art art--flake flake-2" role="img" aria-label="Snowflake decoration"></div>
    <div class="art art--flake flake-3" role="img" aria-label="Snowflake decoration"></div>
    <div class="art art--flake flake-4" role="img" aria-label="Small snowflake decoration"></div>
    <div class="art art--flake flake-5" role="img" aria-label="Small snowflake decoration"></div>

    <div class="art art--hero" role="img" aria-label="Illustrated caped superhero in blue and yellow flying forward with a cool breeze trailing"></div>
    <div class="art art--cube" role="img" aria-label="Glowing ice cube with swirling cold air"></div>
    <div class="art art--house" role="img" aria-label="Family homes at dusk with warm windows, garden and people relaxing on the porch"></div>

    <h1 class="headline">
      <span class="headline__line headline__line--one">Making Your Home <span class="headline__ice">COOL</span></span>
      <span class="headline__line headline__line--two">Look <span class="headline__ice">Easy</span></span>
    </h1>

    <p class="subline">Relax This Summer — <span class="subline__brand">Varnel AC</span> Has You Covered</p>

    <div class="brand brand--full">
      <span class="brand__dot"></span>
      <span class="brand__text">VARNEL<span class="brand__sub">Heating &amp; AC</span></span>
    </div>

    <div class="brand brand--large">
      <span class="brand__dot"></span>
      <span class="brand__text">VARNEL</span>
    </div>

    <p class="tagline">superchill <span class="tagline__link">with</span> Varnel heating</p>
  </main>
</body>
</html>
```